Business Card Design Project for Heron Lending

Hello there,

We are looking for a business card design for our new Heron Lending car financing company. We are looking for a business card that will include:

- An address
- Telephone number and extension
- Employee Name
- Employee Title
- Our logo and name clearly visible

We are including our logo with this writeup, we are looking to convey friendliness, trus and memorability. Colors and everything else is up to you.

Target Market(s)

18-34 year old males and females

Industry/Entity Type

Business

```html
<!DOCTYPE html>
<html lang="en">
<head>
<meta charset="utf-8">
<title>Heron Lending — Business Cards</title>
<link href="https://fonts.googleapis.com/css2?family=Arimo:wght@400;700&display=swap" rel="stylesheet">
<style>
  :root {
    --bg: #d9d9d9;
    --card: #fbfbfb;
    --navy: #2e4f86;
    --navy-deep: #22407a;
    --ink: #1b1b1b;
    --rule: #161616;
  }
  * { margin: 0; padding: 0; box-sizing: border-box; }
  html, body { width: 1200px; height: 864px; overflow: hidden; }
  body {
    background: var(--bg);
    font-family: "Arimo", Arial, sans-serif;
    position: relative;
  }
  .card {
    position: absolute;
    width: 540px;
    height: 310px;
    background: var(--card);
    box-shadow: 0 2px 6px rgba(0,0,0,0.15);
    overflow: hidden;
  }

  /* Back card */
  .card--back { left: 610px; top: 110px; }
  .back-band {
    position: absolute;
    left: 0; top: 178px;
    width: 330px; height: 44px;
    background: var(--navy);
  }
  .back-brand {
    position: absolute;
    left: 350px; top: 176px;
    color: var(--navy);
    font-weight: 400;
    font-size: 26px;
    letter-spacing: 4px;
    line-height: 1.15;
    text-transform: uppercase;
  }
  .back-brand small {
    display: block;
    font-size: 11px;
    letter-spacing: 9px;
  }
  .back-tab {
    position: absolute;
    right: 0; top: 236px;
    width: 26px; height: 34px;
    background: var(--navy);
  }

  /* Front card */
  .card--front { left: 70px; top: 430px; }
  .front-brand {
    position: absolute;
    left: 0; right: 0; top: 44px;
    text-align: center;
    color: var(--navy);
    font-weight: 400;
    font-size: 34px;
    letter-spacing: 6px;
    line-height: 1.1;
    text-transform: uppercase;
  }
  .front-brand small {
    display: block;
    font-size: 12px;
    letter-spacing: 12px;
  }
  .rule {
    position: absolute;
    top: 131px;
    height: 2px;
    background: var(--rule);
  }
  .rule--left { left: 0; width: 150px; }
  .rule--right { right: 0; width: 150px; }
  .person {
    position: absolute;
    left: 0; right: 0; top: 118px;
    text-align: center;
  }
  .person__name {
    color: var(--navy);
    font-weight: 700;
    font-size: 22px;
  }
  .person__title {
    color: var(--ink);
    font-size: 14px;
    margin-top: 2px;
  }
  .contact {
    position: absolute;
    left: 0; right: 0; top: 188px;
    text-align: center;
    color: var(--navy);
    font-size: 14px;
    line-height: 1.55;
  }
  .front-stripes {
    position: absolute;
    left: 0; right: 0; bottom: 22px;
    height: 40px;
    border-top: 2px solid var(--navy);
  }
  .front-stripes::after {
    content: "";
    position: absolute;
    left: 0; right: 0; top: 6px; bottom: 0;
    background: var(--navy-deep);
    border-top: 2px solid var(--card);
  }
</style>
</head>
<body>
  <section class="card card--back" aria-label="Business card back">
    <div class="back-band"></div>
    <div class="back-brand">Heron<small>Lending</small></div>
    <div class="back-tab"></div>
  </section>

  <section class="card card--front" aria-label="Business card front">
    <div class="front-brand">Heron<small>Lending</small></div>
    <div class="rule rule--left"></div>
    <div class="rule rule--right"></div>
    <div class="person">
      <div class="person__name">Employee Name</div>
      <div class="person__title">Managing Director</div>
    </div>
    <div class="contact">
      <div>0012 3456 700</div>
      <div>Your Address Inc 2nd Lane, Ave Larkfield, NJ 00000</div>
    </div>
    <div class="front-stripes"></div>
  </section>
</body>
</html>
```